​Silver Harbor Rhythm provides personal, friendly service in a fun and high energy environment. We are based in Vermont.

We would like a card that appeals to a wide range of audiences as we do a wide range of events. Please feel free to check out our website silverharborrhythm.net for inspiration.

Target Market(s)

weddings, corporate, birthday parties, colleges

Industry/Entity Type

Business

Contact Information for Business Card

Silver Harbor Rhythm
Providing Entertainment For All Occasions
555 274 9160
silverharborrhythm@mailnest.net
silverharborrhythm.net

```html
<!DOCTYPE html>
<html lang="en">
<head>
<meta charset="utf-8">
<title>Silver Harbor Rhythm — Business Card</title>
<link href="https://fonts.googleapis.com/css2?family=Open+Sans:wght@400;600;700&display=swap" rel="stylesheet">
<style>
  :root {
    --stage: #e9e6e1;
    --card-white: #ffffff;
    --brand-green: #2f6a14;
    --rule-dark: #1f2a18;
    --text-grey: #555555;
    --back-dark: #1f0f10;
    --back-text: #ffffff;
    --shadow: rgba(0, 0, 0, 0.22);
  }
  * { box-sizing: border-box; margin: 0; padding: 0; }
  html, body {
    width: 1200px; height: 829px; overflow: hidden;
    background: var(--stage);
    font-family: "Open Sans", Arial, sans-serif;
  }
  .canvas {
    position: relative; width: 1200px; height: 829px;
  }
  .card {
    position: absolute; top: 255px;
    width: 530px; height: 303px;
    box-shadow: 0 8px 22px var(--shadow);
    overflow: hidden;
  }
  /* Front */
  .card-front { left: 50px; background: var(--card-white); }
  .front-top { position: absolute; inset: 0 0 122px 0; }
  .holder { position: absolute; right: 28px; top: 30px; text-align: right; }
  .holder-name { color: var(--brand-green); font-weight: 700; font-size: 15px; }
  .holder-title { color: var(--text-grey); font-size: 10px; margin-top: 2px; }
  .brand-lockup {
    position: absolute; left: 32px; top: 100px;
    display: flex; align-items: center; gap: 10px;
  }
  .brand-mark { width: 16px; height: 16px; background: var(--brand-green); }
  .brand-name {
    color: var(--brand-green); font-weight: 700; font-size: 22px;
    letter-spacing: 1px; text-transform: uppercase;
  }
  .band-rule {
    position: absolute; left: 0; right: 0; bottom: 122px;
    height: 3px; background: var(--rule-dark);
  }
  .front-band {
    position: absolute; left: 0; right: 0; bottom: 0; height: 119px;
    background: var(--brand-green); color: var(--card-white);
    display: flex; align-items: center; padding: 0 30px;
  }
  .contact-list { list-style: none; font-size: 12.5px; line-height: 1.9; }
  .contact-list li { display: flex; align-items: center; gap: 8px; }
  .contact-list svg { width: 12px; height: 12px; flex: none; }
  .band-divider { width: 1px; height: 56px; background: rgba(255,255,255,0.7); margin: 0 18px; }
  .address { font-size: 11.5px; line-height: 1.7; }
  /* Back */
  .card-back { left: 620px; background: var(--back-dark); color: var(--back-text); }
  .back-lockup {
    position: absolute; left: 0; right: 0; top: 105px;
    display: flex; justify-content: center; align-items: center; gap: 12px;
  }
  .back-mark { width: 20px; height: 20px; background: var(--back-text); }
  .back-name { font-weight: 700; font-size: 26px; letter-spacing: 1px; text-transform: uppercase; }
  .back-url {
    position: absolute; left: 0; right: 0; bottom: 62px;
    text-align: center; font-size: 15px; letter-spacing: 1px;
  }
</style>
</head>
<body>
<main class="canvas">
  <section class="card card-front" aria-label="Card front">
    <div class="front-top">
      <div class="holder">
        <p class="holder-name">Your Name</p>
        <p class="holder-title">Title</p>
      </div>
      <div class="brand-lockup">
        <span class="brand-mark"></span>
        <span class="brand-name">Silver Harbor Rhythm</span>
      </div>
    </div>
    <div class="band-rule"></div>
    <div class="front-band">
      <ul class="contact-list">
        <li>
          <svg viewBox="0 0 12 12"><circle cx="6" cy="6" r="5.5" fill="none" stroke="#fff"/><path d="M4 3.2c-.6.4-.7 1.2-.2 2.3.6 1.3 1.6 2.4 2.8 3 .8.4 1.3.3 1.7-.2l-1-1-.7.4c-.6-.3-1.2-1-1.5-1.6l.4-.7z" fill="#fff"/></svg>
          555 274 9160
        </li>
        <li>
          <svg viewBox="0 0 12 12"><circle cx="6" cy="6" r="5.5" fill="#fff"/><rect x="3" y="4" width="6" height="4" fill="none" stroke="#2f6a14" stroke-width="0.8"/><path d="M3 4l3 2.2L9 4" fill="none" stroke="#2f6a14" stroke-width="0.8"/></svg>
          silverharborrhythm@mailnest.net
        </li>
        <li>
          <svg viewBox="0 0 12 12"><circle cx="6" cy="6" r="5.5" fill="#fff"/><circle cx="6" cy="6" r="3.3" fill="none" stroke="#2f6a14" stroke-width="0.7"/><path d="M2.7 6h6.6M6 2.7v6.6" stroke="#2f6a14" stroke-width="0.7"/></svg>
          www.silverharborrhythm.net
        </li>
      </ul>
      <div class="band-divider"></div>
      <p class="address">Sreet Name, City Name<br>Zip Code-00000</p>
    </div>
  </section>

  <section class="card card-back" aria-label="Card back">
    <div class="back-lockup">
      <span class="back-mark"></span>
      <span class="back-name">Silver Harbor Rhythm</span>
    </div>
    <p class="back-url">www.silverharborrhythm.net</p>
  </section>
</main>
</body>
</html>
```